Business Card Design Project

We are an incubator company that helps young entrepreneur to launch new ideas into the market. We will be targeting investors or likewise; Angels, young entrepreneurs and technopreneurs.

Our logo is being tasked by pixelhive to design, therefore there is no logo for now.
You can us Lanternfield Pte Ltd as the logo for the time being.

Please let us have some versions of modern and yet professional designs; for words, you can indicate e.g (address), (Title)

thanks

Target Market(s)

young entrepreneurs
angels, investors

Industry/Entity Type

Business

Colors
3176b5
ffffff

Requirements
Must have
• able to project out our name; Lanternfield
Should not have
• Nothing childish or cartoon

```html
<!DOCTYPE html>
<html lang="en">
<head>
<meta charset="utf-8">
<title>Lanternfield Business Card</title>
<link rel="stylesheet" href="https://fonts.googleapis.com/css2?family=Arimo:wght@400;700&display=swap">
<style>
  :root {
    --brand: #3176b5;
    --brand-deep: #1b4f91;
    --brand-light: #4a93d6;
    --paper: #ffffff;
    --ink: #1a1a1a;
    --backdrop: #eef1f5;
  }
  * { margin: 0; padding: 0; box-sizing: border-box; }
  html, body {
    width: 1200px; height: 784px; overflow: hidden;
    background: var(--backdrop);
    font-family: "Arimo", Arial, sans-serif;
  }
  .stage {
    position: relative; width: 1200px; height: 784px;
    display: flex; align-items: center; justify-content: center; gap: 48px;
  }
  .card {
    position: relative; width: 530px; height: 303px;
    box-shadow: 0 6px 18px rgba(0,0,0,0.12);
  }
  /* Front */
  .card-front {
    background: radial-gradient(ellipse at 50% 40%, var(--brand-light) 0%, var(--brand) 45%, var(--brand-deep) 100%);
    display: flex; flex-direction: column; align-items: center; justify-content: center;
    color: var(--paper);
  }
  .brand-mark {
    width: 58px; height: 58px; border-radius: 10px;
    background: var(--paper); margin-bottom: 22px;
  }
  .brand-name {
    font-weight: 700; font-size: 46px; letter-spacing: 1px; text-transform: uppercase; line-height: 1;
  }
  .brand-tagline {
    margin-top: 6px; font-size: 12px; letter-spacing: 3.5px; text-transform: uppercase; line-height: 1.2;
  }
  /* Back */
  .card-back {
    background: var(--paper);
    border: 9px solid var(--brand);
  }
  .card-back::before {
    content: ""; position: absolute; inset: 8px;
    border: 2px solid var(--brand);
  }
  .holder {
    position: absolute; top: 18px; right: 24px; text-align: right;
  }
  .holder-name { color: var(--brand); font-weight: 700; font-size: 16px; }
  .holder-title { color: var(--ink); font-size: 11px; margin-top: 2px; }
  .card-back .logo {
    position: absolute; top: 56px; left: 0; right: 0;
    display: flex; flex-direction: column; align-items: center; color: var(--brand);
  }
  .card-back .brand-mark { width: 40px; height: 40px; border-radius: 7px; background: var(--brand); margin-bottom: 12px; }
  .card-back .brand-name { font-size: 30px; }
  .card-back .brand-tagline { font-size: 8px; letter-spacing: 2.4px; margin-top: 4px; }
  .contacts {
    position: absolute; left: 24px; bottom: 18px; list-style: none;
  }
  .contacts li {
    display: flex; align-items: center; gap: 8px;
    font-size: 15px; color: var(--ink); line-height: 21px;
  }
  .contacts svg { width: 16px; height: 16px; fill: var(--brand); flex: none; }
</style>
</head>
<body>
<main class="stage">
  <section class="card card-front">
    <div class="brand-mark"></div>
    <div class="brand-name">Lanternfield</div>
    <div class="brand-tagline">Launching Ideas To Market</div>
  </section>

  <section class="card card-back">
    <div class="holder">
      <div class="holder-name">Maren Holt</div>
      <div class="holder-title">Manager</div>
    </div>
    <div class="logo">
      <div class="brand-mark"></div>
      <div class="brand-name">Lanternfield</div>
      <div class="brand-tagline">Launching Ideas To Market</div>
    </div>
    <ul class="contacts">
      <li>
        <svg viewBox="0 0 16 16" aria-hidden="true"><path d="M3.5 1 6 3.6 4.7 5.5c.9 2 2.6 3.8 4.8 4.8L11.4 9 14 11.5 12.4 14C6.8 13.6 2.4 9.2 2 3.6Z"/></svg>
        415 208 7731
      </li>
      <li>
        <svg viewBox="0 0 16 16" aria-hidden="true"><path d="M8 1a7 7 0 1 0 0 14A7 7 0 0 0 8 1Zm0 1.5c.9 0 1.8 1.6 2.1 4H5.9c.3-2.4 1.2-4 2.1-4ZM2.6 7.5h2.1a13 13 0 0 0 0 1H2.6a5.6 5.6 0 0 1 0-1Zm3.3 0h4.2a12 12 0 0 1 0 1H5.9a12 12 0 0 1 0-1Zm5.4 0h2.1a5.6 5.6 0 0 1 0 1h-2.1a13 13 0 0 0 0-1ZM5.9 9.5h4.2c-.3 2.4-1.2 4-2.1 4s-1.8-1.6-2.1-4Z"/></svg>
        www.lanternfield.com
      </li>
      <li>
        <svg viewBox="0 0 16 16" aria-hidden="true"><path d="M1 3.5h14v9H1Zm1.4 1L8 8.6l5.6-4.1Z"/></svg>
        maren@lanternfield.com
      </li>
      <li>
        <svg viewBox="0 0 16 16" aria-hidden="true"><path d="M8 1.5 1 7.8h2.2V14.5h3.6v-4h2.4v4h3.6V7.8H15Z"/></svg>
        Harbourview, Singapore
      </li>
    </ul>
  </section>
</main>
</body>
</html>
```